TALMORK

The business want a professional looking business card. We have a scetch we will add but want the extra upgrade, and would like more suggestions for variations of our business cards.

```html
<!DOCTYPE html>
<html lang="en">
<head>
<meta charset="utf-8">
<title>TALMORK Business Cards</title>
<link rel="stylesheet" href="https://fonts.googleapis.com/css2?family=Cinzel:wght@500;700&family=Montserrat:wght@400;600&display=swap">
<style>
  :root {
    --canvas: #ffffff;
    --card: #151515;
    --card-edge: #0b0b0b;
    --gold: #c9a248;
    --gold-soft: #b38a3c;
    --frame: #9c7d35;
  }
  * { margin: 0; padding: 0; box-sizing: border-box; }
  html, body { width: 1200px; height: 2457px; overflow: hidden; background: var(--canvas); }
  .sheet { position: relative; width: 1200px; height: 2457px; }
  .card {
    position: absolute; left: 189px; width: 880px; height: 502px;
    background: radial-gradient(ellipse at 50% 45%, #1c1c1c 0%, var(--card) 60%, var(--card-edge) 100%);
    box-shadow: 12px 18px 30px rgba(0,0,0,0.28);
  }
  .card-front { top: 640px; }
  .card-back { top: 1282px; }
  .card-frame {
    position: absolute; inset: 10px; border: 1px solid var(--frame);
  }
  .brand-name {
    font-family: "Cinzel", serif; font-weight: 500; color: var(--gold);
    letter-spacing: 0.28em; text-align: center; position: absolute;
  }
  .card-front .brand-name { left: 0; right: 0; top: 250px; font-size: 68px; padding-left: 0.28em; }
  .front-web {
    position: absolute; left: 0; right: 0; top: 392px; text-align: center;
    font-family: "Montserrat", sans-serif; font-size: 30px; letter-spacing: 0.16em;
    color: var(--gold-soft);
  }
  .front-web strong { font-weight: 600; color: var(--gold); }
  .holder-name {
    position: absolute; left: 76px; top: 86px;
    font-family: "Cinzel", serif; font-weight: 700; font-size: 43px; color: var(--gold);
    letter-spacing: 0.01em;
  }
  .holder-role {
    position: absolute; left: 77px; top: 150px;
    font-family: "Montserrat", sans-serif; font-size: 31px; color: var(--gold-soft);
  }
  .contact-list { position: absolute; left: 74px; top: 258px; list-style: none; }
  .contact-item {
    display: flex; align-items: center; gap: 12px; height: 50px;
    font-family: "Montserrat", sans-serif; font-size: 26px; color: var(--gold-soft);
  }
  .contact-icon { width: 26px; height: 26px; flex: none; }
  .card-back .brand-name { left: 560px; width: 270px; top: 325px; font-size: 34px; }
</style>
</head>
<body>
<main class="sheet">
  <section class="card card-front" aria-label="Card front">
    <div class="card-frame"></div>
    <div class="brand-name">TALMORK</div>
    <div class="front-web">www.<strong>talmork</strong>.llc</div>
  </section>

  <section class="card card-back" aria-label="Card back">
    <div class="card-frame"></div>
    <h1 class="holder-name">AKSEL BRANDVIK</h1>
    <p class="holder-role">CEO &amp; Founder</p>
    <ul class="contact-list">
      <li class="contact-item">
        <svg class="contact-icon" viewBox="0 0 26 26" aria-hidden="true">
          <circle cx="13" cy="13" r="13" fill="var(--gold)"/>
          <rect x="9" y="6" width="8" height="14" rx="1.5" fill="none" stroke="#151515" stroke-width="1.6"/>
          <line x1="12" y1="17.5" x2="14" y2="17.5" stroke="#151515" stroke-width="1.4"/>
        </svg>
        004791234567
      </li>
      <li class="contact-item">
        <svg class="contact-icon" viewBox="0 0 26 26" aria-hidden="true">
          <circle cx="13" cy="13" r="13" fill="var(--gold)"/>
          <rect x="6.5" y="8.5" width="13" height="9" fill="none" stroke="#151515" stroke-width="1.6"/>
          <polyline points="6.5,8.5 13,14 19.5,8.5" fill="none" stroke="#151515" stroke-width="1.6"/>
        </svg>
        talmork.llc@postmail.com
      </li>
      <li class="contact-item">
        <svg class="contact-icon" viewBox="0 0 26 26" aria-hidden="true">
          <circle cx="13" cy="13" r="13" fill="var(--gold)"/>
          <circle cx="13" cy="13" r="6.5" fill="none" stroke="#151515" stroke-width="1.5"/>
          <ellipse cx="13" cy="13" rx="2.8" ry="6.5" fill="none" stroke="#151515" stroke-width="1.3"/>
          <line x1="6.5" y1="13" x2="19.5" y2="13" stroke="#151515" stroke-width="1.3"/>
        </svg>
        www.talmork.llc
      </li>
    </ul>
    <div class="brand-name">TALMORK</div>
  </section>
</main>
</body>
</html>
```